Maple Grove Schools | brand new stationery!

We need stationery design with our new logo! Our company updated it's name and image and we like to incorporate the new one on our stationery, business cards and email signature. We are looking for fresh, new ideas!
Industry: Childcare, Elementary and Middle School
Company Name: Maple Grove Schools
Tagline: Bright Futures Start Here
Main colors: Blue, white and a little yellow
Star shape is something new for us! Do you see a way to incorporate it as a design element?

```html
<!DOCTYPE html>
<html lang="en">
<head>
<meta charset="utf-8">
<title>Maple Grove Schools — Stationery</title>
<link href="https://fonts.googleapis.com/css2?family=Poppins:wght@400;500;600&family=Roboto+Slab:wght@400&display=swap" rel="stylesheet">
<style>
  :root {
    --navy: #0a1c6e;
    --yellow: #fcc31c;
    --ink: #1d1d26;
    --paper: #ffffff;
    --backdrop: #dcdcdc;
    --rule: #2a2a2a;
  }
  html, body { margin: 0; padding: 0; overflow: hidden; }
  body { width: 1200px; height: 749px; background: var(--backdrop); position: relative; }
  .sheet { position: absolute; background: var(--paper); box-shadow: 1px 1px 2px rgba(0,0,0,.35); overflow: hidden; }
  .band-top { position: absolute; left: 0; right: 0; top: 0; background: var(--navy); }
  .band-bottom { position: absolute; left: 0; right: 0; bottom: 0; background: var(--yellow); }
  .brand { position: absolute; display: flex; align-items: center; gap: 6px;
           font-family: "Poppins", sans-serif; font-weight: 500; color: var(--ink); white-space: nowrap; }
  .brand-dot { border-radius: 50%; background: var(--navy); flex: none; }
  .contact { position: absolute; font-family: "Roboto Slab", serif; color: var(--ink); white-space: nowrap; }
  .contact-item { position: absolute; display: flex; align-items: center; }
  .icon { flex: none; background: var(--navy); display: flex; align-items: center; justify-content: center; }
  .icon svg { width: 70%; height: 70%; }
  .rule { position: absolute; height: 1px; background: var(--rule); }

  /* letterhead */
  .letterhead { left: 388px; top: 133px; width: 370px; height: 479px; }
  .letterhead .band-top { height: 8px; }
  .letterhead .band-bottom { height: 6px; }
  .letterhead .brand { left: 0; right: 0; top: 146px; top: 14px; justify-content: center; font-size: 16px; }
  .letterhead .brand-dot { width: 22px; height: 22px; }
  .letterhead .rule { left: 27px; width: 320px; top: 444px; }
  .letterhead .contact { font-size: 8px; line-height: 10px; }
  .letterhead .icon { width: 15px; height: 15px; margin-right: 4px; }

  /* business card */
  .card { left: 161px; top: 335px; width: 347px; height: 105px; }
  .card .band-top { height: 4px; }
  .card .band-bottom { height: 4px; }
  .card .person { position: absolute; left: 18px; top: 16px; font-family: "Poppins", sans-serif; }
  .card .person-name { font-size: 8.5px; font-weight: 500; color: var(--navy); line-height: 11px; }
  .card .person-role { font-family: "Roboto Slab", serif; font-size: 6.5px; color: var(--ink); line-height: 9px; }
  .card .contact { font-size: 6.5px; line-height: 9px; }
  .card .icon { width: 9px; height: 9px; margin-right: 4px; }
  .card .rule { left: 18px; width: 236px; top: 71px; }
  .card .brand { left: 252px; width: 92px; top: 18px; flex-direction: column; gap: 3px;
                 font-size: 13px; line-height: 13px; text-align: center; }
  .card .brand-dot { width: 18px; height: 18px; }

  /* envelope front */
  .envelope-front { left: 799px; top: 231px; width: 295px; height: 147px; }
  .envelope-front .band-top { height: 5px; }
  .envelope-front .band-bottom { height: 4px; }
  .envelope-front .brand { left: 14px; top: 7px; font-size: 11.5px; gap: 5px; }
  .envelope-front .brand-dot { width: 17px; height: 17px; }
  .envelope-front .rule { left: 14px; width: 254px; top: 116px; }
  .envelope-front .contact { font-size: 6px; line-height: 8px; }
  .envelope-front .icon { width: 12px; height: 12px; margin-right: 3px; }

  /* envelope back */
  .envelope-back { left: 799px; top: 387px; width: 295px; height: 148px; box-shadow: 0 1px 0 #555; }
  .envelope-back .flap { position: absolute; left: 0; top: 0; width: 295px; height: 35px; }
</style>
</head>
<body>
<svg width="0" height="0" style="position:absolute">
  <defs>
    <symbol id="i-phone" viewBox="0 0 24 24"><path fill="#fff" d="M6.6 10.8a15 15 0 0 0 6.6 6.6l2.2-2.2c.3-.3.7-.4 1-.2 1.1.4 2.3.6 3.6.6.6 0 1 .4 1 1V20c0 .6-.4 1-1 1A17 17 0 0 1 3 4c0-.6.4-1 1-1h3.5c.6 0 1 .4 1 1 0 1.3.2 2.5.6 3.6.1.3 0 .7-.2 1z"/></symbol>
    <symbol id="i-mobile" viewBox="0 0 24 24"><rect x="7" y="2" width="10" height="20" rx="2" fill="none" stroke="#fff" stroke-width="2"/><circle cx="12" cy="18" r="1.2" fill="#fff"/></symbol>
    <symbol id="i-mail" viewBox="0 0 24 24"><rect x="3" y="6" width="18" height="12" fill="none" stroke="#fff" stroke-width="2"/><path d="M3 6l9 7 9-7" fill="none" stroke="#fff" stroke-width="2"/></symbol>
    <symbol id="i-globe" viewBox="0 0 24 24"><g fill="none" stroke="#fff" stroke-width="1.8"><circle cx="12" cy="12" r="9"/><ellipse cx="12" cy="12" rx="4" ry="9"/><path d="M3 12h18M5 7h14M5 17h14"/></g></symbol>
    <symbol id="i-pin" viewBox="0 0 24 24"><path fill="#fff" d="M12 2a7 7 0 0 0-7 7c0 5 7 13 7 13s7-8 7-13a7 7 0 0 0-7-7zm0 9.5A2.5 2.5 0 1 1 12 6.5a2.5 2.5 0 0 1 0 5z"/></symbol>
  </defs>
</svg>

<!-- Letterhead -->
<section class="sheet letterhead">
  <div class="band-top"></div>
  <div class="brand"><span class="brand-dot"></span>Maple Grove Schools</div>
  <div class="rule"></div>
  <div class="contact">
    <div class="contact-item" style="left:27px;top:452px"><span class="icon"><svg><use href="#i-phone"/></svg></span><span>055-210 384 672<br>055-210 384 672</span></div>
    <div class="contact-item" style="left:117px;top:451px"><span class="icon"><svg><use href="#i-globe"/></svg></span><span>office@maplegrove.org<br>www.maplegrove.org</span></div>
    <div class="contact-item" style="left:235px;top:451px"><span class="icon"><svg><use href="#i-pin"/></svg></span><span>Your Address line here<br>Country Code 0123456</span></div>
  </div>
  <div class="band-bottom"></div>
</section>

<!-- Business card -->
<section class="sheet card">
  <div class="band-top"></div>
  <div class="person">
    <div class="person-name">Daniel Reyes</div>
    <div class="person-role">Managing Director</div>
  </div>
  <div class="contact">
    <div class="contact-item" style="left:18px;top:45px"><span class="icon"><svg><use href="#i-phone"/></svg></span>055-210 384 672</div>
    <div class="contact-item" style="left:18px;top:54px"><span class="icon"><svg><use href="#i-mobile"/></svg></span>055-210 384 672</div>
    <div class="contact-item" style="left:92px;top:45px"><span class="icon"><svg><use href="#i-mail"/></svg></span>office@maplegrove.org</div>
    <div class="contact-item" style="left:92px;top:54px"><span class="icon"><svg><use href="#i-globe"/></svg></span>www.maplegrove.org</div>
    <div class="contact-item" style="left:18px;top:78px"><span class="icon"><svg><use href="#i-pin"/></svg></span>Your Address line here, Country Code 0123456</div>
  </div>
  <div class="rule"></div>
  <div class="brand"><span class="brand-dot"></span><span>Maple Grove<br>Schools</span></div>
  <div class="band-bottom"></div>
</section>

<!-- Envelope front -->
<section class="sheet envelope-front">
  <div class="band-top"></div>
  <div class="brand"><span class="brand-dot"></span>Maple Grove Schools</div>
  <div class="rule"></div>
  <div class="contact">
    <div class="contact-item" style="left:14px;top:121px"><span class="icon"><svg><use href="#i-phone"/></svg></span><span>055-210 384 672<br>055-210 384 672</span></div>
    <div class="contact-item" style="left:85px;top:121px"><span class="icon"><svg><use href="#i-globe"/></svg></span><span>office@maplegrove.org<br>www.maplegrove.org</span></div>
    <div class="contact-item" style="left:180px;top:121px"><span class="icon"><svg><use href="#i-pin"/></svg></span><span>Your Address line here<br>Country Code 0123456</span></div>
  </div>
  <div class="band-bottom"></div>
</section>

<!-- Envelope back -->
<section class="sheet envelope-back">
  <svg class="flap" viewBox="0 0 295 35" preserveAspectRatio="none" aria-hidden="true">
    <polygon points="0,0 295,0 284,35 12,35" fill="var(--navy)"/>
  </svg>
</section>
</body>
</html>
```